Business card for law firm

Need business card for new law firm. Think confident, authoritative, conservative, but not stuffy or old-fashioned.

Contact Information for Business Card

Content for card - logo (uploaded), plus the following:

Paul Whitcombe (larger font)
Managing Partner (larger font, but not as large as name)
Level 9, 7 Ferris Lane
Sydney NSW 2000
Main Tel 02 9364 2710
Direct Tel 02 8472 3159
Email paul@qvlegal.com.au
www.qvlegal.com.au

Letterhead design should include logo plus:
Level 9, 7 Ferris Lane
Sydney NSW 2000
Tel 02 8472 3159
www.qvlegal.com.au

```html
<!DOCTYPE html>
<html lang="en">
<head>
<meta charset="utf-8">
<title>Quayvale Lawyers – Business Card</title>
<link href="https://fonts.googleapis.com/css2?family=Cinzel:wght@400;600&family=Open+Sans:wght@400;600&display=swap" rel="stylesheet">
<style>
  :root {
    --stage: #e4e5e8;
    --paper: #ffffff;
    --navy: #0b1f5c;
    --ink: #0a0a0a;
    --white: #ffffff;
    --shadow: rgba(0, 0, 0, 0.18);
  }
  * { box-sizing: border-box; margin: 0; padding: 0; }
  html, body {
    width: 1200px;
    height: 960px;
    overflow: hidden;
    background: var(--stage);
  }
  .stage {
    position: relative;
    width: 1200px;
    height: 960px;
  }
  .card {
    position: absolute;
    left: 280px;
    width: 640px;
    height: 392px;
    overflow: hidden;
    box-shadow: 0 10px 30px var(--shadow);
  }
  .card--front { top: 70px; background: var(--paper); }
  .card--back  { top: 498px; background: var(--ink); }

  /* Front */
  .brand {
    position: absolute;
    left: 44px;
    top: 70px;
    display: flex;
    align-items: center;
    gap: 12px;
    color: var(--navy);
    font-family: "Open Sans", sans-serif;
    font-weight: 600;
    font-size: 26px;
    line-height: 1;
  }
  .brand__mark {
    width: 26px;
    height: 26px;
    background: var(--navy);
    flex: none;
  }
  .band {
    position: absolute;
    inset: 0;
    background: var(--navy);
    clip-path: polygon(0 51%, 100% 37%, 100% 100%, 0 100%);
  }
  .title-tab {
    position: absolute;
    right: 0;
    top: 168px;
    width: 250px;
    padding: 12px 22px 12px 24px;
    background: var(--ink);
    border-radius: 12px 0 0 12px;
    color: var(--white);
    font-family: "Cinzel", serif;
    text-align: right;
  }
  .title-tab__name {
    display: block;
    font-size: 19px;
    font-weight: 600;
    line-height: 1.25;
    white-space: nowrap;
  }
  .title-tab__role {
    display: block;
    font-size: 15px;
    font-weight: 400;
    line-height: 1.3;
    white-space: nowrap;
  }
  .contact {
    position: absolute;
    left: 40px;
    top: 214px;
    list-style: none;
    color: var(--white);
    font-family: "Open Sans", sans-serif;
    font-size: 14px;
    line-height: 22px;
  }
  .contact__item {
    display: flex;
    align-items: center;
    gap: 6px;
  }
  .contact__icon {
    width: 12px;
    height: 12px;
    fill: var(--white);
    flex: none;
  }
  .contact__address { margin-top: 10px; }

  /* Back */
  .back-brand {
    position: absolute;
    left: 0;
    right: 0;
    top: 150px;
    text-align: center;
    color: var(--white);
    font-family: "Open Sans", sans-serif;
    font-weight: 600;
    font-size: 34px;
    line-height: 1.2;
  }
  .back-url {
    position: absolute;
    left: 0;
    right: 0;
    top: 300px;
    text-align: center;
    color: var(--white);
    font-family: "Open Sans", sans-serif;
    font-size: 13px;
    letter-spacing: 0.3em;
  }
</style>
</head>
<body>
<main class="stage">

  <section class="card card--front" aria-label="Business card front">
    <div class="band"></div>

    <div class="brand">
      <span class="brand__mark"></span>
      <span class="brand__name">Quayvale Lawyers</span>
    </div>

    <div class="title-tab">
      <span class="title-tab__name">Paul Whitcombe</span>
      <span class="title-tab__role">Managing Partner</span>
    </div>

    <ul class="contact">
      <li class="contact__item">
        <svg class="contact__icon" viewBox="0 0 24 24"><path d="M6.6 10.8a15.1 15.1 0 0 0 6.6 6.6l2.2-2.2a1 1 0 0 1 1-.25 11.4 11.4 0 0 0 3.6.57 1 1 0 0 1 1 1V20a1 1 0 0 1-1 1A17 17 0 0 1 3 4a1 1 0 0 1 1-1h3.5a1 1 0 0 1 1 1c0 1.25.2 2.45.57 3.6a1 1 0 0 1-.25 1z"/></svg>
        02 9364 2710
      </li>
      <li class="contact__item">
        <svg class="contact__icon" viewBox="0 0 24 24"><path d="M6.6 10.8a15.1 15.1 0 0 0 6.6 6.6l2.2-2.2a1 1 0 0 1 1-.25 11.4 11.4 0 0 0 3.6.57 1 1 0 0 1 1 1V20a1 1 0 0 1-1 1A17 17 0 0 1 3 4a1 1 0 0 1 1-1h3.5a1 1 0 0 1 1 1c0 1.25.2 2.45.57 3.6a1 1 0 0 1-.25 1z"/></svg>
        02 8472 3159
      </li>
      <li class="contact__item">
        <svg class="contact__icon" viewBox="0 0 24 24"><path d="M2 5h20v14H2z M2 5l10 8 10-8" fill="none" stroke="#fff" stroke-width="2.4"/></svg>
        paul@qvlegal.com.au
      </li>
      <li class="contact__item">
        <svg class="contact__icon" viewBox="0 0 24 24"><circle cx="12" cy="12" r="10" fill="none" stroke="#fff" stroke-width="2.4"/><path d="M2 12h20M12 2c3 3 3 17 0 20M12 2c-3 3-3 17 0 20" fill="none" stroke="#fff" stroke-width="2"/></svg>
        www.qvlegal.com.au
      </li>
      <li class="contact__item contact__address">Level 9, 7 Ferris Lane, Sydney NSW 2000</li>
    </ul>
  </section>

  <section class="card card--back" aria-label="Business card back">
    <div class="back-brand">Quayvale Lawyers</div>
    <div class="back-url">www.qvlegal.com.au</div>
  </section>

</main>
</body>
</html>
```